Seeking funky, innovative business cards

I am looking to refresh our current business cards to something more engaging, visual and impactful. We are a management consultancy firm, see website (www.larkstone-partners.com.au). I've included our colour scheme, sample of the slides we use and our old business cards. We would like our cards to have icons. The card should display:- Name- Title- Mobile number- Address- Email address- Website - Company logo- Our purpose statement "We build workplaces where people love to grow"

Contact Information for Business Card

Brennan Ulfsson
Consultant
0468 927 341
Level 3, 218 Wexley Street, Melbourne 3000
brennan@larkstone-partners.com.au
www.larkstone-partners.com.au

Purpose statement "We build workplaces where people love to grow"
LOGO available in google images

Font styles to use
Other font styles liked:
• Open Sans Light, Bebas Neue (open to other cool foints)

Colors
ffc214
5c5c5c
f5f5f5
fefefe

Requirements
Must have
• - Name
• - Title
• - Mobile number
• - Address
• - Email address
• - Website
• - Company logo
• - Our purpose statement "We build workplaces where people love to grow"
Nice to have
• - Icons
• - Colour (see our colour scheme"

```html
<!DOCTYPE html>
<html lang="en">
<head>
<meta charset="utf-8">
<title>Larkstone Partners – Business Card</title>
<link rel="stylesheet" href="https://fonts.googleapis.com/css2?family=Lato:wght@300;400;700&family=Noto+Serif:ital@1&display=swap">
<style>
  :root {
    --page: #ffffff;
    --card-light: #ffffff;
    --card-dark: #45484a;
    --ink: #3a3d3f;
    --yellow: #ffc214;
    --orange: #f39a2a;
    --tagline: #e0a21c;
    --white: #fefefe;
  }
  * { margin: 0; padding: 0; box-sizing: border-box; }
  html, body { width: 1200px; height: 1176px; overflow: hidden; background: var(--page); }
  body { position: relative; font-family: "Lato", sans-serif; color: var(--ink); }

  .card {
    position: absolute;
    left: 290px;
    width: 601px;
    height: 344px;
    border-radius: 20px;
    overflow: hidden;
    box-shadow: 0 6px 10px rgba(0,0,0,0.22);
  }
  .card--front { top: 231px; background: var(--card-light); }
  .card--back { top: 622px; background: var(--card-dark); }

  .holder { position: absolute; left: 32px; top: 25px; }
  .holder__name { font-size: 26px; font-weight: 400; letter-spacing: -0.2px; line-height: 30px; }
  .holder__title { font-family: "Noto Serif", serif; font-style: italic; font-size: 14px; color: var(--orange); line-height: 18px; }
  .holder__rule { width: 27px; height: 4px; background: var(--orange); margin-top: 16px; }

  .brand { position: absolute; display: flex; align-items: center; gap: 10px; white-space: nowrap; }
  .brand__dot { width: 12px; height: 12px; border-radius: 50%; background: var(--yellow); flex: none; }
  .brand__name { font-weight: 400; }
  .card--front .brand { right: 32px; top: 84px; }
  .card--front .brand__name { font-size: 33px; color: var(--ink); letter-spacing: -0.5px; }
  .card--back .brand { left: 0; right: 0; top: 172px; justify-content: center; }
  .card--back .brand__name { font-size: 44px; color: var(--white); letter-spacing: -0.8px; }

  .contacts { position: absolute; left: 31px; top: 204px; list-style: none; }
  .contacts li { display: flex; align-items: center; height: 25px; font-size: 15px; }
  .contacts svg { width: 14px; height: 14px; margin-right: 10px; flex: none; }

  .footer-shape { position: absolute; left: 0; top: 0; width: 601px; height: 344px; }
  .address {
    position: absolute; left: 32px; top: 293px; height: 20px;
    display: flex; align-items: center; font-size: 14.5px; color: var(--white);
  }
  .address svg { width: 12px; height: 14px; margin-right: 12px; }

  .tagline {
    position: absolute; left: 0; right: 0; top: 298px;
    text-align: center; font-size: 13.5px; color: var(--tagline);
  }
</style>
</head>
<body>

<section class="card card--front" aria-label="Business card front">
  <svg class="footer-shape" viewBox="0 0 601 344" aria-hidden="true">
    <defs>
      <linearGradient id="band" x1="0" x2="1" y1="0" y2="0">
        <stop offset="0" stop-color="#ffc214"/>
        <stop offset="1" stop-color="#f39a2a"/>
      </linearGradient>
    </defs>
    <path d="M0,316 L368,316 C398,316 405,286 440,286 L601,286 L601,344 L0,344 Z" fill="var(--card-dark)"/>
    <path d="M0,293 L390,293 C374,299 368,313 350,313 L0,313 Z" fill="url(#band)"/>
  </svg>

  <div class="holder">
    <h1 class="holder__name">Brennan Ulfsson</h1>
    <p class="holder__title">Consultant</p>
    <div class="holder__rule"></div>
  </div>

  <div class="brand">
    <span class="brand__dot"></span>
    <span class="brand__name">Larkstone Partners</span>
  </div>

  <ul class="contacts">
    <li>
      <svg viewBox="0 0 14 14" aria-hidden="true"><path d="M1 5 C1 2 13 2 13 5 L10 6 L9.5 4.5 C8 4 6 4 4.5 4.5 L4 6 Z" fill="#f39a2a"/><path d="M3 7 L11 7 L12 11 L2 11 Z" fill="#f39a2a"/><circle cx="7" cy="9" r="1.3" fill="#fff"/></svg>
      0468 927 341
    </li>
    <li>
      <svg viewBox="0 0 14 14" aria-hidden="true"><rect x="1" y="3" width="12" height="8.5" fill="#f39a2a"/><path d="M1 3 L7 8 L13 3" fill="none" stroke="#fff" stroke-width="1"/></svg>
      brennan@larkstone-partners.com.au
    </li>
    <li>
      <svg viewBox="0 0 14 14" aria-hidden="true"><g fill="none" stroke="#f7b96a" stroke-width="1"><circle cx="7" cy="7" r="5.5"/><ellipse cx="7" cy="7" rx="2.4" ry="5.5"/><path d="M1.5 7 H12.5 M2.5 4 H11.5 M2.5 10 H11.5"/></g></svg>
      www.larkstone-partners.com.au
    </li>
  </ul>

  <div class="address">
    <svg viewBox="0 0 12 14" aria-hidden="true"><path d="M6 0.5 C2.8 0.5 1 2.8 1 5 C1 8 6 13.5 6 13.5 C6 13.5 11 8 11 5 C11 2.8 9.2 0.5 6 0.5 Z" fill="var(--card-dark)"/><circle cx="6" cy="5" r="1.8" fill="#ffc214"/></svg>
    Level 3, 218 Wexley Street,&nbsp; Melbourne 3000
  </div>
</section>

<section class="card card--back" aria-label="Business card back">
  <div class="brand">
    <span class="brand__dot"></span>
    <span class="brand__name">Larkstone Partners</span>
  </div>
  <p class="tagline">We build workplaces where people love to grow</p>
</section>

</body>
</html>
```